Business Card Design

We like to use greens as you will see in our logo (but not TOO much green). We are a Dental Clinic in a somewhat eccentric community. We do not like the dated sharp designs which we see many dentists use. We're looking for something bright and fresh while still maintaining the integrity of the profession. Elegance is not necessarily what we are going for... we need for the design to be "mature" but also up-lifting.

See our logo.
Updates

Project Deadline Extended
Reason: We have 5 designs which we like. But we'd like to see a few more before committing to a design.

Project Deadline Extended
Reason: We are awaiting revisions to this project. We are still welcoming designs while we wait to see if designers are able to provide to us the revisions we require in order to proceed with a selection.

Target Market(s)

Younger families - ages late 20's to early 40's

Industry/Entity Type

Business

Contact Information for Business Card

Corwel T. Banfry DDS 2730 W. Halvert Rd. Ste. 7 Royal Oak, MI 48391 (248)555-0174 FX (248)555-0189 info@BrightwellDentalCareMi.com BrigthwellDentalCareMi.com on the back of the card we need an appointment reminder (For____ Date___ Time____) with "If you are unable to keep your appointment, kindly give 48 hours notice" at the bottom. No use of teeth in the design. DOUBLE SIDED DESIGN

Requirements
Should not have
• The use of pictures of teeth

```html
<!DOCTYPE html>
<html lang="en">
<head>
<meta charset="utf-8">
<title>Brightwell Dental Care — Business Card</title>
<link rel="stylesheet" href="https://fonts.googleapis.com/css2?family=Source+Sans+3:ital,wght@0,400;0,600;0,700;1,400&family=Cinzel:wght@500&display=swap">
<style>
  :root {
    --green-deep: #1c6b36;
    --green-text: #1f6b35;
    --green-soft: #a9d39a;
    --white: #ffffff;
    --ink: #2b2b2b;
    --line: #6f6f6f;
    --page: #eeeeea;
  }
  * { box-sizing: border-box; margin: 0; padding: 0; }
  html, body { width: 1200px; height: 1182px; overflow: hidden; }
  body {
    background: var(--page);
    font-family: "Source Sans 3", "Helvetica Neue", Arial, sans-serif;
    position: relative;
  }

  /* ---------- front side ---------- */
  .card-front {
    position: absolute; left: 233px; top: 49px;
    width: 943px; height: 538px;
    background: var(--green-deep);
    overflow: hidden;
  }
  .brand-tab {
    position: absolute; left: 524px; top: 19px;
    width: 419px; height: 223px;
    background: var(--white);
    border-radius: 90px 0 0 90px;
    display: flex; flex-direction: column; align-items: center; justify-content: center;
    color: var(--green-text); font-weight: 600; line-height: 1;
  }
  .brand-name { font-size: 56px; letter-spacing: 0.5px; }
  .brand-sub { font-size: 34px; letter-spacing: 2px; margin-top: 10px; }

  .identity-tab {
    position: absolute; left: 0; top: 292px;
    width: 534px; height: 216px;
    background: var(--white);
    border-radius: 0 84px 84px 0;
  }
  .person-name {
    position: absolute; right: 29px; top: 26px;
    font-size: 50px; font-weight: 700; color: var(--green-text);
    white-space: nowrap;
  }
  .person-title {
    position: absolute; right: 29px; top: 92px;
    font-size: 34px; color: var(--ink);
  }
  .person-email {
    position: absolute; right: 33px; top: 162px;
    font-size: 22px; color: var(--ink);
    display: flex; align-items: center; gap: 8px; white-space: nowrap;
  }

  .contact-list {
    position: absolute; left: 604px; top: 296px;
    color: var(--white); font-size: 23px; line-height: 1;
    list-style: none;
  }
  .contact-list li { display: flex; align-items: center; gap: 6px; height: 34px; margin-bottom: 7px; }
  .contact-list .web { margin-bottom: 14px; }
  .contact-list .address { display: block; height: auto; line-height: 1.3; }
  .icon { width: 18px; height: 18px; flex: none; }

  /* ---------- back side ---------- */
  .card-back {
    position: absolute; left: 28px; top: 615px;
    width: 942px; height: 536px;
    background: var(--white);
    border: 1.5px solid #9a9a9a;
    overflow: hidden;
    color: var(--ink);
  }
  .back-accent {
    position: absolute; left: 318px; top: 63px;
    width: 296px; height: 296px;
  }
  .appt-heading {
    position: absolute; left: 0; width: 942px; top: 92px;
    text-align: center;
    font-family: "Cinzel", "Times New Roman", serif;
    font-weight: 500; font-size: 33px; color: var(--green-text);
  }
  .field { position: absolute; font-size: 25px; white-space: nowrap; }
  .dots { position: absolute; border-bottom: 2px dotted var(--line); height: 0; }

  .slot-row { position: absolute; left: 335px; top: 289px; display: flex; gap: 14px; }
  .slot { width: 170px; height: 36px; border: 2px solid #555; border-radius: 6px; background: rgba(255,255,255,0.4); }

  .weekdays {
    position: absolute; left: 71px; top: 380px; width: 800px;
    display: flex; justify-content: space-between; align-items: center;
    font-size: 26px; font-weight: 700; color: #111;
  }
  .day { display: flex; align-items: center; gap: 10px; }
  .day-box { width: 56px; height: 34px; border: 2px solid #555; border-radius: 5px; background: var(--white); }

  .notice {
    position: absolute; left: 0; width: 942px; top: 460px;
    text-align: center; font-style: italic; font-size: 26px; color: #222;
  }
</style>
</head>
<body>

<section class="card-front" aria-label="Business card, front">
  <div class="brand-tab">
    <span class="brand-name">Brightwell</span>
    <span class="brand-sub">DENTAL CARE</span>
  </div>

  <div class="identity-tab">
    <h1 class="person-name">Corwel T. Banfry</h1>
    <p class="person-title">DDS</p>
    <p class="person-email">
      <svg class="icon" viewBox="0 0 20 20" aria-hidden="true"><rect x="1" y="4" width="18" height="13" rx="2" fill="#1f6b35"/><path d="M2 5l8 6 8-6" stroke="#fff" stroke-width="1.8" fill="none"/></svg>
      info@BrightwellDentalCareMi.com
    </p>
  </div>

  <ul class="contact-list">
    <li>
      <svg class="icon" viewBox="0 0 20 20" aria-hidden="true"><circle cx="10" cy="10" r="8.5" fill="none" stroke="#fff" stroke-width="1.5"/><path d="M7 5l2 3-1.3 1.2c.6 1.4 1.6 2.4 3 3L12 11l3 2-1 2c-4 0-8-4-8-8z" fill="#fff"/></svg>
      (248)555-0174
    </li>
    <li>
      <svg class="icon" viewBox="0 0 20 20" aria-hidden="true"><rect x="5" y="3" width="10" height="6" fill="none" stroke="#fff" stroke-width="1.6"/><rect x="2" y="9" width="16" height="7" rx="1.5" fill="#fff"/></svg>
      (248)555-0189
    </li>
    <li class="web">
      <svg class="icon" viewBox="0 0 20 20" aria-hidden="true"><g fill="none" stroke="#fff" stroke-width="1.4"><circle cx="10" cy="10" r="8"/><ellipse cx="10" cy="10" rx="3.5" ry="8"/><path d="M2 10h16M3.5 6h13M3.5 14h13"/></g></svg>
      BrigthwellDentalCareMi.com
    </li>
    <li class="address">2730 W. Halvert Rd.<br>Ste. 7 Royal Oak, MI 48391</li>
  </ul>
</section>

<section class="card-back" aria-label="Business card, back: appointment reminder">
  <svg class="back-accent" viewBox="0 0 296 296" aria-hidden="true"><circle cx="148" cy="148" r="148" fill="#a9d39a" opacity="0.35"/></svg>

  <h2 class="appt-heading">YOUR APPOINTMENT</h2>

  <span class="field" style="left:75px; top:160px;">Name :</span>
  <span class="dots" style="left:179px; top:182px; width:683px;"></span>

  <span class="field" style="left:75px; top:226px;">Date :</span>
  <span class="dots" style="left:180px; top:248px; width:234px;"></span>
  <span class="field" style="left:423px; top:226px;">Time :</span>
  <span class="dots" style="left:507px; top:248px; width:250px;"></span>
  <span class="field" style="left:762px; top:226px;">am / pm</span>

  <span class="field" style="left:75px; top:292px;">Next Appointment</span>
  <div class="slot-row">
    <span class="slot"></span><span class="slot"></span><span class="slot"></span>
  </div>

  <div class="weekdays">
    <span class="day">MON <span class="day-box"></span></span>
    <span class="day">TUE <span class="day-box"></span></span>
    <span class="day">WED <span class="day-box"></span></span>
    <span class="day">THU <span class="day-box"></span></span>
    <span class="day">FRI <span class="day-box"></span></span>
    <span class="day">SAT <span class="day-box"></span></span>
  </div>

  <p class="notice">If you are unable to keep your appointment, kindly give 48 hours notice</p>
</section>

</body>
</html>
```